We need a home page design only (no coding necessary) for a motorcycle dealer. He wants the theme to be Modern-Industrial with vintage details. Please read the requirements below.

Client likes http://www.pelicanbaymotorworks.example/ and wants a similar layout.

Dealer info:
Lone Ridge Cycle Depot (logo attached)
210.555.0187
384 W Calloway Ln Ste 207
San Antonio, TX 78299
Hours
Sun-Mon: Closed
Tue-Sat: 9a – 6p

Slideshow images - I've attached a few so you can see his inventory, it may help with the design

Call-to-action buttons:
Financing
Sell Your Bike
View Inventory

Theme: Modern-Industrial with Vintage details
Main background: Artistic or vintage image of motorcycle (see link for examples from client: http://instagram.com/copperandgale#)
Content background: likes the use of 'black wood' on http://www.pelicanbaymotorworks.example - find a way to incorporate the wood background somewhere on the design

Accent Colors: Black, white and pops of red
Featured Vehicles location: Middle (in between the call-to-action buttons and the verbiage)
Social Networking: Facebook, Instagram

Client likes http://www.pelicanbaymotorworks.example/ and wants a similar layout:
-wants the navigation bar above the banner/header
-wants the logo centered in the banner/header (open to the placement of the phone number, address and social media icons, as long as they show in the banner)
-wants to leave gaps between the sections so the background is visible

Attachments:
-layout that the client provided (LRCD_HOME_PAGE)
-logo (LRCD_BLACK & LRCD_W)
-psd file showing the typical layout used (sample-site) - ONLY A SUGGESTION!
-a few slideshow images to show client's inventory (the rest of the files)

Please let me know if you have any questions and thank you in advance for your work.

Thank you all for your wonderful mockups. I've sent them to the client and am awaiting the response. I will keep you all updated. Best regards, Marjorie

Thank you all, I am just waiting for feedback from the client. I will post the feedback as soon as I get a response from the client. Best regards, Marjorie

```html
<!DOCTYPE html>
<html lang="en">
<head>
<meta charset="utf-8">
<title>Lone Ridge Cycle Depot</title>
<link rel="stylesheet" href="https://fonts.googleapis.com/css2?family=Jost:wght@400;500;600&display=swap">
<style>
:root{
  --ink:#0b0b0b;
  --panel:#151515;
  --wood:#262626;
  --wood-dark:#1c1c1c;
  --frame:#4a4a4a;
  --white:#ffffff;
  --muted:#b5b5b5;
  --red:#e4161b;
}
*{box-sizing:border-box;margin:0;padding:0}
html,body{width:866px;height:1200px;overflow:hidden}
body{position:relative;font-family:"Jost",sans-serif;color:var(--white);background:var(--ink)}
.backdrop{position:absolute;inset:0;background:radial-gradient(ellipse at 50% 30%,#3a3a3a 0%,#1e1e1e 45%,#0d0d0d 100%)}
.abs{position:absolute}
/* nav */
.main-nav{left:0;top:0;width:866px;height:37px;background:linear-gradient(#1a1a1a,#0c0c0c);border-bottom:1px solid #333;display:flex;justify-content:center;align-items:center;gap:13px;font-size:10px;letter-spacing:.2px}
.main-nav .star{color:#888;font-size:9px}
/* header */
.hours{left:53px;top:73px;font-size:10px;line-height:15px}
.label-red{color:var(--red)}
.hours .hint{color:var(--muted)}
.brand-mark{left:357px;top:50px;width:154px;height:76px;border:2px solid var(--white);border-radius:10px;display:flex;align-items:center;justify-content:center;text-align:center;font-weight:600;font-size:13px;line-height:16px;letter-spacing:1px;background:var(--ink)}
.connect{left:726px;top:73px;font-size:10px}
.social{display:flex;gap:5px;margin-top:4px}
.social span{width:18px;height:18px;border-radius:50%;background:#666}
.social span:nth-child(4){background:var(--red)}
.address-line{left:0;top:138px;width:866px;text-align:center;font-size:9.5px;color:var(--muted)}
/* slider */
.slider{left:53px;top:162px;width:760px;height:296px;border:3px solid var(--frame);background:linear-gradient(135deg,#cfc8b8 0%,#8b8d95 40%,#2b2540 65%,#bfc0c4 100%)}
.dots{left:395px;top:424px;width:76px;height:24px;background:rgba(0,0,0,.75);border-radius:6px 6px 0 0;display:flex;gap:5px;justify-content:center;align-items:center}
.dots i{width:9px;height:9px;border-radius:50%;background:var(--white)}
.dots i:first-child{background:var(--red)}
/* cta */
.cta{top:475px;width:239px;height:151px;background:#2a2a2a;border:2px solid #3c3c3c}
.cta .photo{position:absolute;left:7px;top:8px;width:221px;height:108px}
.cta .label{position:absolute;left:7px;bottom:8px;font-size:12.5px;letter-spacing:.3px}
.cta svg{position:absolute;right:7px;bottom:10px}
/* brands */
.brands{left:53px;top:642px;width:760px;height:60px;background:var(--ink);border:1px solid #333;display:flex;align-items:center;padding:0 18px;gap:44px;font-size:15px;font-weight:600}
.brands .title{font-size:12.5px;font-weight:500}
.brands .name{color:#cfcfcf}
/* welcome */
.welcome{left:53px;top:720px;width:760px;height:210px;background:repeating-linear-gradient(90deg,var(--wood) 0 38px,var(--wood-dark) 38px 40px,#2c2c2c 40px 90px,var(--wood-dark) 90px 92px);border:1px solid #333}
.welcome h1{position:absolute;left:14px;top:18px;font-size:17px;font-weight:400}
.welcome .copy{position:absolute;left:14px;top:50px;width:525px;font-size:9px;line-height:15.5px;color:#c8c8c8}
.welcome .copy p{margin-bottom:3px}
.welcome .more{position:absolute;left:14px;top:176px;font-size:9.5px}
.contact-card{left:625px;top:742px;width:173px;height:165px;background:var(--ink);border:1px solid #444;text-align:center}
.contact-card h2{font-size:16px;font-weight:400;margin-top:12px}
.contact-card .mini-mark{margin:10px auto 0;width:78px;height:34px;border:1.5px solid var(--white);border-radius:6px;font-size:7px;font-weight:600;line-height:9px;display:flex;align-items:center;justify-content:center}
.contact-card .addr{font-size:8.5px;color:var(--muted);line-height:14px;margin-top:9px}
.contact-card .phone{font-size:12.5px;margin-top:7px}
/* featured */
.featured{left:53px;top:950px;width:760px;height:153px;background:var(--ink);border:1px solid #333}
.featured h2{position:absolute;left:22px;top:42px;font-size:16px;font-weight:400;line-height:22px}
.featured .arrows{position:absolute;left:46px;top:96px}
.thumb{top:965px;width:139px;height:124px;background:#333}
.thumb .photo{height:94px}
.thumb .bar{height:30px;background:var(--red);display:flex;gap:4px;justify-content:center;align-items:center}
.thumb .bar span{width:17px;height:17px;border:1.5px solid var(--white)}
/* footer */
.site-footer{left:0;top:1120px;width:866px;height:80px;background:#141414;border-top:1px solid #2b2b2b}
.foot-mark{left:53px;top:1131px;width:67px;height:34px;border:1.5px solid var(--white);border-radius:6px;font-size:7px;font-weight:600;line-height:9px;display:flex;align-items:center;justify-content:center;text-align:center}
.foot-links{right:53px;top:1133px;font-size:8.5px;color:var(--red)}
.copyright{left:53px;top:1174px;font-size:8.5px;color:#9a9a9a}
</style>
</head>
<body>
<div class="backdrop" role="img" aria-label="Moody black-and-white photograph of a vintage motorcycle filling the page background"></div>

<nav class="main-nav abs">
  <span>HOME</span><span class="star">★</span><span>INVENTORY</span><span class="star">★</span><span>VEHICLE FINDER</span><span class="star">★</span><span>ABOUT US</span><span class="star">★</span><span>FINANCING</span><span class="star">★</span><span>SERVICE</span><span class="star">★</span><span>SOLD INVENTORY</span><span class="star">★</span><span>CONTACT US</span>
</nav>

<div class="hours abs"><div class="label-red">HOURS:</div><div><span class="hint">Sun-Mon:</span> Closed &nbsp;&nbsp;|&nbsp;&nbsp; <span class="hint">Tue-Sat:</span> 9am – 6pm</div></div>
<div class="brand-mark abs">LONE RIDGE<br>CYCLE DEPOT</div>
<div class="connect abs"><div class="label-red">CONNECT US:</div><div class="social"><span></span><span></span><span></span><span></span></div></div>
<div class="address-line abs">384 W CALLOWAY LN STE 207 &nbsp;&nbsp;&nbsp;|&nbsp;&nbsp;&nbsp; SAN ANTONIO, TX 78299</div>

<div class="slider abs" role="img" aria-label="Slideshow photo of a purple and chrome touring motorcycle parked by a garage door"></div>
<div class="dots abs"><i></i><i></i><i></i><i></i></div>

<a class="cta abs" style="left:53px"><div class="photo" role="img" aria-label="Close-up of a motorcycle speedometer" style="background:linear-gradient(135deg,#bfc3c8,#e9e6da 50%,#6d6f73)"></div><span class="label">FINANCING</span><svg width="12" height="12" viewBox="0 0 12 12"><circle cx="6" cy="6" r="5" fill="none" stroke="#fff"/><path d="M5 3.5 7.5 6 5 8.5" fill="none" stroke="#fff" stroke-width="1.3"/></svg></a>
<a class="cta abs" style="left:314px"><div class="photo" role="img" aria-label="Front view of a black cruiser motorcycle headlight" style="background:linear-gradient(135deg,#8a8578,#1d1d1d 55%,#9b9b9b)"></div><span class="label">SELL YOUR BIKE</span><svg width="12" height="12" viewBox="0 0 12 12"><circle cx="6" cy="6" r="5" fill="none" stroke="#fff"/><path d="M5 3.5 7.5 6 5 8.5" fill="none" stroke="#fff" stroke-width="1.3"/></svg></a>
<a class="cta abs" style="left:574px"><div class="photo" role="img" aria-label="Red touring motorcycle fairing and handlebars" style="background:linear-gradient(135deg,#d9d4c8,#c0141a 55%,#e2e2e2)"></div><span class="label">VIEW INVENTORY</span><svg width="12" height="12" viewBox="0 0 12 12"><circle cx="6" cy="6" r="5" fill="none" stroke="#fff"/><path d="M5 3.5 7.5 6 5 8.5" fill="none" stroke="#fff" stroke-width="1.3"/></svg></a>

<section class="brands abs">
  <span class="title">BRANDS:</span>
  <span class="name">KESTREL</span><span class="name">RAVENNA</span><span class="name">HOLLOWAY</span><span class="name">SORANO</span><span class="name">DRAVO</span><span class="name">HALDEN</span>
</section>

<section class="welcome abs">
  <h1>WELCOME TO <span class="label-red">LONE RIDGE CYCLE DEPOT</span></h1>
  <div class="copy">
    <p>Aliquam molestie, mi et imperdiet euismod, dui purus auctor tellus, et interdum lacus lectus et ante. Sed accumsan sollicitudin sapien, sit amet adipiscing turpis gravida ac. In congue, neque ac lobortis volutpat, libero mauris varius mi, vitae suscipit ipsum ligula vitae risus. Duis aliquam nibh a dui iaculis viverra id a velit. Vivamus egestas risus in magna varius commodo. Sed semper viverra egestas. Etiam pretium porttitor lectus, vel ornare neque porta volutpat.</p>
    <p>Aenean a nibh eget turpis vehicula tempus ac sed massa. Vestibulum dolor nulla, ultrices ac tincidunt sed, laoreet non est. Suspendisse lobortis turpis in odio blandit ac interdum lorem euismod. Etiam risus massa, vulputate eu pellentesque et, consectetur a neque.</p>
  </div>
  <span class="more">LEARN MORE ››</span>
</section>
<aside class="contact-card abs">
  <h2>CONTACT US</h2>
  <div class="mini-mark">LONE RIDGE<br>CYCLE DEPOT</div>
  <div class="addr">384 W Calloway Ln Ste 207<br>San Antonio, TX 78299</div>
  <div class="phone">Ph: 210.555.0187</div>
</aside>

<section class="featured abs">
  <h2>FEATURED<br><span class="label-red">VEHICLES</span></h2>
  <svg class="arrows" width="34" height="14" viewBox="0 0 34 14"><path d="M8 1 2 7l6 6M26 1l6 6-6 6" fill="none" stroke="#fff" stroke-width="1.6"/></svg>
</section>
<div class="thumb abs" style="left:174px"><div class="photo" role="img" aria-label="Purple touring motorcycle" style="background:linear-gradient(135deg,#cfcac0,#2d2844 55%,#aaa)"></div><div class="bar"><span></span><span></span></div></div>
<div class="thumb abs" style="left:334px"><div class="photo" role="img" aria-label="Black cruiser motorcycle" style="background:linear-gradient(135deg,#9a958a,#1a1a1a 55%,#888)"></div><div class="bar"><span></span><span></span></div></div>
<div class="thumb abs" style="left:495px"><div class="photo" role="img" aria-label="Chrome engine of a custom motorcycle" style="background:linear-gradient(135deg,#b8b8b8,#3a3a3a 55%,#cfcfcf)"></div><div class="bar"><span></span><span></span></div></div>
<div class="thumb abs" style="left:655px"><div class="photo" role="img" aria-label="Red touring motorcycle" style="background:linear-gradient(135deg,#ddd8cc,#c1151b 55%,#e0e0e0)"></div><div class="bar"><span></span><span></span></div></div>

<footer class="site-footer abs"></footer>
<div class="foot-mark abs">LONE RIDGE<br>CYCLE DEPOT</div>
<div class="foot-links abs">Home &nbsp;|&nbsp; Inventory &nbsp;|&nbsp; Site Map &nbsp;|&nbsp; Contact Us</div>
<div class="copyright abs">Copyright © 2014. All Right Reserved &nbsp;|&nbsp; Privacy Policy</div>
</body>
</html>
```